Small Business Directory Site Requires a Professional Responsive Web Design

Small Business Directory and Coupon Site - we require a complete website design for a brand new responsive & mobile friendly website. We already have a coder who will professional code our website in Magento.

All PSD pages need to be professionally designed then uploaded into a sharedrive (i.e. like filecrate). Additionally, as I cannot pre-empt everything, please note that we may require a little more assistance once the files have been transferred (for example, in www.brightlane-listings.example if you hover your mouse on the search box you will see a pop up box. We want one of these too and I think that means there may be extra design work here)

We have some draft page sketches have been created (there are some minor changes we want to the sketches provided though); however, we require an excellent designer to add the creative touches to it to make it look professionally created. All artwork/font must be legal.

-------------------------
We like the look of the www.brightlane-listings.example and www. marlowfolio.example

For the headers, please consider a font similar to RNS camellia. We likes this style, but it is too thin for the headers...so we need a variation like this one. For the copy/general text font, something basic that marries well with the headers.

---------------------

Please be sure to also read the brief we wrote for the coder as this will help with better understanding our design requirements.

In total I believe we have about 50 pages. This includes all the little pages and most of the pop up boxes (but not the little help key boxes). For example, pages include...

1. Login (this is where customers log in and can edit, manage their profiles. This means that there are backend membership pages)
2. Mini Services (same look and feel as the business coupons)
3. Resource Centre
4. Join (this is where customers learn about the packages available to submit a directory listing, if they ‘buy’ a package (i.e. free, $25 or $150 package) then they can create their own directory listing)
5. Search the directory (customer can view all the categories and also search the directory)
6. Create a directory listing (this is where customers learn about the packages available to submit a directory listing, if they ‘buy’ a package (i.e. free, $25 or $150 package) then they can create their own directory listing)
7. Quote finder (also know as Get a Quote)
8. Coupons (customer go to the business coupon page and can view all current coupons/submit a coupon)
9. Submit a coupon (form)
10.Advertise with us (form)
11. Join the forum
12.Submit an article or video (form)
13. Affiliates (listing of affiliates we currently have)
14. Become an affiliate (form)
15. Case studies (customer can view the case studies we have in the resource centre)
16. Help Guides (customer can view the help guides we have in the resource centre)
17. About Us
18 .Contact Us (form)
19. Terms & Condition
20. Privacy Policy
21. Supporting City Councils
22. Site Map
23. Forgot password / login details
24. Homepage
25. If we hover over a few areas (i.e. search box, location field) it pops up with more information.
etc etc etc. . . there are more pages.

Please see our filecrate link for the draft mock up pages that I have created so far.

https://www.cloudtrunk.example/sh/qk72pmw4rtz8nd/KLMvbTq2fWndxPzs8Yh4ecRQu

We are in a rush! We'd like to get the majority of the artwork completed by the end of the month. Minor fixes/tweaks can occur thereafter.

Target Market(s)

Small Businesses (employees 0 - 50) located throughout Australia

Industry/Entity Type

Business

Font styles to use
Sans Serif

Requirements
Must have
• Professional. Artwork must be legal (cannot be cut and paste or taken off other websites, must be legally purchased and used).Must look contemporary, fresh, modern.

Absolutely must be a responsive site!
Nice to have
• original work, original photos, original art.

like modern, fresh photos that demonstrate innovation, growth, small business, Australian scenery, stability, goals/passion.
Should not have
• cut and paste graphics, illegal graphics, not purchased graphics.

```html
<!DOCTYPE html>
<html lang="en">
<head>
<meta charset="utf-8">
<title>Harbourline Link — Small Business Directory</title>
<link href="https://fonts.googleapis.com/css2?family=Questrial&family=Lato:wght@400;700&display=swap" rel="stylesheet">
<style>
:root{
  --orange:#f7901e;
  --orange-text:#f28a1a;
  --ink:#333;
  --grey:#666;
  --line:#dcdcdc;
  --bar:#1f1f1f;
  --footer:#000;
  --footer-bottom:#2a2a2a;
  --partner-bg:#f1f1f1;
}
*{box-sizing:border-box;margin:0;padding:0}
html,body{width:778px;height:1200px;overflow:hidden;background:#fff}
body{position:relative;font-family:"Lato",sans-serif;color:var(--ink)}
.abs{position:absolute}
.heading{font-family:"Questrial",sans-serif}

/* header */
.site-header{position:absolute;left:0;top:0;width:778px;height:70px;background:#fff}
.brand{position:absolute;left:84px;top:21px;display:flex;align-items:center;gap:8px;font-family:"Questrial",sans-serif;font-size:19px;color:var(--ink);white-space:nowrap}
.brand-mark{width:15px;height:15px;border-radius:50%;background:var(--orange)}
.main-nav{position:absolute;left:285px;top:30px;display:flex;font-family:"Questrial",sans-serif;font-size:10px;color:#222;white-space:nowrap}
.main-nav span{padding:0 8px;border-left:1px solid #ccc;line-height:12px}
.main-nav span:first-child{border-left:none}

/* hero */
.hero{position:absolute;left:0;top:70px;width:778px;height:303px;overflow:hidden;
  background:
    radial-gradient(ellipse 260px 120px at 470px 40px,rgba(255,236,170,.95),rgba(255,200,110,0) 70%),
    linear-gradient(100deg,rgba(120,82,40,.55) 0%,rgba(120,82,40,0) 22%,rgba(120,82,40,0) 70%,rgba(130,70,20,.5) 100%),
    linear-gradient(180deg,#f2b35e 0%,#e89a3c 28%,#d9842a 48%,#b8865a 60%,#8d8378 74%,#9a9288 88%,#7f776c 100%)}
.hero-road{position:absolute;left:150px;top:170px;width:420px;height:140px;
  background:radial-gradient(ellipse 210px 140px at 50% 100%,rgba(150,145,140,.85),rgba(150,145,140,0) 75%)}
.hero-title{position:absolute;left:84px;top:126px;font-family:"Questrial",sans-serif;font-weight:400;font-size:27px;color:#fff;white-space:nowrap}
.hero-sub{position:absolute;left:84px;top:163px;font-family:"Questrial",sans-serif;font-size:13px;color:#fff;white-space:nowrap}
.search-bar{position:absolute;left:83px;top:146px;width:357px;height:42px;background:var(--orange);border-radius:2px}
.search-field{position:absolute;top:11px;height:20px;background:#fff;font-size:7px;color:#888;padding:6px 8px;white-space:nowrap}
.search-btn{position:absolute;left:271px;top:11px;width:23px;height:20px;background:#111}
.join-btn{position:absolute;left:300px;top:11px;width:57px;height:20px;background:#111;color:#fff;font-family:"Questrial",sans-serif;font-size:10px;text-align:center;line-height:20px}
.resource-panel{position:absolute;left:514px;top:45px;width:181px;height:209px;background:rgba(90,80,75,.78);border-radius:3px;color:#fff}
.resource-panel h2{font-family:"Questrial",sans-serif;font-weight:400;font-size:17px;text-align:center;margin-top:16px;white-space:nowrap}
.resource-panel .tag{font-family:"Questrial",sans-serif;font-size:8.5px;text-align:center;margin-top:2px}
.panel-photo{position:absolute;left:37px;top:58px;width:111px;height:68px;border:3px solid #2b2b2b;
  background:radial-gradient(circle at 40% 45%,#ffffff,#dfe7ef 45%,#a9bccd 100%)}
.panel-cat{position:absolute;left:16px;top:146px;font-size:7px;color:var(--orange);white-space:nowrap}
.panel-desc{position:absolute;left:16px;top:156px;font-size:7px;white-space:nowrap}
.panel-price{position:absolute;left:17px;top:176px;font-family:"Questrial",sans-serif;font-size:13px;white-space:nowrap}
.panel-price small{font-size:7px}
.panel-btn{position:absolute;left:93px;top:177px;width:64px;height:16px;background:var(--orange);font-size:7px;text-align:center;line-height:16px}
.dots{position:absolute;left:370px;top:288px;display:flex;gap:3px}
.dots i{width:8px;height:8px;border-radius:50%;background:#fff;opacity:.9}

/* category bar */
.cat-bar{position:absolute;left:0;top:373px;width:778px;height:27px;background:var(--bar)}
.cat-list{position:absolute;left:82px;top:0;display:flex;height:27px;font-family:"Questrial",sans-serif;font-size:8.2px;color:#fff;white-space:nowrap}
.cat-list span{padding:0 5.6px;line-height:27px;border-right:1px solid #444}
.cat-list .all{background:var(--orange);border:none;padding:0 8px}

/* community */
.section-title{position:absolute;left:0;width:778px;text-align:center;font-family:"Questrial",sans-serif;font-weight:400;font-size:20px;color:#333}
.col-title{position:absolute;width:220px;text-align:center;font-family:"Questrial",sans-serif;font-size:13px;line-height:18px;color:var(--orange-text)}
.col-media{position:absolute;border:1px solid var(--line)}
.col-text{position:absolute;text-align:center;font-size:7.5px;line-height:13.2px;color:var(--grey)}
.btn{position:absolute;background:var(--orange);color:#fff;font-family:"Questrial",sans-serif;font-size:8px;text-align:center;border-radius:2px}
.divider{position:absolute;left:83px;top:746px;width:613px;height:1px;background:var(--line)}

/* coupons */
.coupon{position:absolute;top:797px;width:129px;height:124px;border:1px solid var(--line);text-align:center}
.coupon-art{position:absolute;left:26px;top:18px;width:77px;height:44px;border:1px solid rgba(0,0,0,.12)}
.coupon h3{position:absolute;left:0;width:100%;top:72px;font-family:"Questrial",sans-serif;font-weight:400;font-size:10px;color:var(--orange-text)}
.coupon p{position:absolute;left:0;width:100%;top:87px;font-size:7.5px;color:var(--grey)}
.coupon .price{position:absolute;left:0;width:100%;top:100px;font-family:"Questrial",sans-serif;font-size:12px;color:#111}

/* partners */
.partners{position:absolute;left:0;top:943px;width:778px;height:50px;background:var(--partner-bg)}
.partner{position:absolute;top:13px;font-family:"Questrial",sans-serif;font-size:20px;color:#a5a5a5;white-space:nowrap}

/* footer */
.site-footer{position:absolute;left:0;top:993px;width:778px;height:167px;background:var(--footer)}
.f-col{position:absolute;top:27px}
.f-col h4{font-family:"Questrial",sans-serif;font-weight:400;font-size:10px;color:var(--orange);margin-bottom:8px;white-space:nowrap}
.f-col li{list-style:none;font-size:7.5px;color:#fff;line-height:14px;white-space:nowrap}
.social{display:flex;gap:6px;margin-top:2px}
.social i{width:16px;height:16px;border-radius:2px}
.subscribe{margin-top:15px;width:126px;height:19px;background:var(--orange);color:#111;font-size:7.5px;text-align:center;line-height:19px}
.footer-bottom{position:absolute;left:0;top:1160px;width:778px;height:40px;background:var(--footer-bottom)}
.footer-bottom p{position:absolute;left:90px;top:16px;font-size:7.5px;color:#8a8a8a}
</style>
</head>
<body>

<header class="site-header">
  <div class="brand"><span class="brand-mark"></span>Harbourline Link</div>
  <nav class="main-nav">
    <span>Login</span><span>Join</span><span>Coupons</span><span>Mini Service</span><span>Get a Quote</span><span>Advertise</span><span>Resource Centre</span>
  </nav>
</header>

<section class="hero">
  <div class="abs" style="left:0;top:0;width:778px;height:303px" role="img" aria-label="Winding mountain road through golden autumn trees at sunset"></div>
  <div class="hero-road"></div>
  <h1 class="hero-title">It's a Brand New Day.</h1>
  <p class="hero-sub">Do More of What Your Love</p>
  <div class="search-bar" style="top:200px">
    <div class="search-field" style="left:13px;width:135px">What are you looking for?</div>
    <div class="search-field" style="left:153px;width:113px">Where?</div>
    <div class="search-btn">
      <svg width="23" height="20" viewBox="0 0 23 20"><circle cx="10.5" cy="9" r="4.2" fill="none" stroke="#fff" stroke-width="1.6"/><line x1="13.5" y1="12" x2="16" y2="14.5" stroke="#fff" stroke-width="1.8"/></svg>
    </div>
    <div class="join-btn">Join Us</div>
  </div>
  <aside class="resource-panel">
    <h2>Resources Centre</h2>
    <p class="tag">Morbi porta libero ullamcorper</p>
    <svg class="abs" style="left:14px;top:86px" width="10" height="16" viewBox="0 0 10 16"><polyline points="8,1 2,8 8,15" fill="none" stroke="#fff" stroke-width="1.3"/></svg>
    <svg class="abs" style="left:157px;top:86px" width="10" height="16" viewBox="0 0 10 16"><polyline points="2,1 8,8 2,15" fill="none" stroke="#fff" stroke-width="1.3"/></svg>
    <div class="panel-photo" role="img" aria-label="Laptop screen showing a business network diagram"></div>
    <div class="abs" style="left:30px;top:126px;width:125px;height:4px;background:#3a3a3a;border-radius:0 0 3px 3px"></div>
    <div class="panel-cat">3 CATEGORY LISTING</div>
    <div class="panel-desc">Lorem ipsum dolor sit amet consectetuer adip</div>
    <div class="panel-price">A $25/<small>YEAR</small></div>
    <div class="panel-btn">CLICK HERE</div>
  </aside>
  <div class="dots"><i></i><i></i><i></i><i></i></div>
</section>

<nav class="cat-bar">
  <div class="cat-list">
    <span>Banking, Finance &amp; Insurance</span><span>Marketing, Design, Photography, Video &amp; Print</span><span>Coaching &amp; Training</span><span>Technology</span><span>Legal</span><span>Administration</span><span class="all">View All Category</span>
  </div>
</nav>

<h2 class="section-title" style="top:420px">Get Real Support from Our Community</h2>

<div class="col-title" style="left:79px;top:466px">How Did You Sort<br>Your Business?</div>
<div class="col-media" style="left:96px;top:508px;width:185px;height:104px;background:radial-gradient(ellipse at 25% 35%,#6f7780 0%,#9aa3ad 22%,#e9edf1 45%),linear-gradient(160deg,#f3f5f7,#c9d6e2)" role="img" aria-label="Hands with a tablet, glasses and printed charts on a white desk"></div>
<p class="col-text" style="left:101px;top:620px;width:175px">Text: Learn from Dana Merrow, a real small business owner. How she started her business and what are the valuable resources for her right now.</p>
<div class="btn" style="left:151px;top:689px;width:75px;height:21px;line-height:21px">CASE STUDY</div>

<div class="col-title" style="left:288px;top:466px">Why Go with<br>Harbourline Link?</div>
<div class="col-media" style="left:309px;top:508px;width:181px;height:104px;background:radial-gradient(ellipse at 75% 60%,#2e3d57 0%,#4b5c78 30%,rgba(200,210,220,0) 60%),linear-gradient(120deg,#e6ebf0,#b7c2cd)" role="img" aria-label="Two colleagues discussing work at a laptop, video preview">
  <svg class="abs" style="left:77px;top:39px" width="26" height="26" viewBox="0 0 26 26"><circle cx="13" cy="13" r="13" fill="#fff"/><polygon points="10,8 18,13 10,18" fill="#111"/></svg>
</div>
<p class="col-text" style="left:305px;top:617px;width:189px">What small business owner can't relate to the ongoing task of attracting new customers? Struggling with cash flow? Or how about not having enough time in the day? It's obvious that small businesses suffer from a lack of support. And that's where we come in</p>
<div class="btn" style="left:346px;top:701px;width:108px;height:21px;line-height:21px">WHITEBOARD VIDEO</div>

<div class="col-title" style="left:484px;top:478px">Become an Affiliate</div>
<div class="col-media" style="left:516px;top:511px;width:169px;height:97px;background:#fff">
  <div class="abs heading" style="left:0;width:167px;top:40px;display:flex;justify-content:center;align-items:center;gap:6px;font-size:13px;color:#1a3f7a;white-space:nowrap"><span style="width:11px;height:11px;border-radius:50%;background:#1a3f7a"></span>Keelstone Insurance</div>
</div>
<p class="col-text" style="left:518px;top:619px;width:168px">If you have a network of small businesses, let us help to create additional value for your members and make money for your network. Talk to us today about how we can help.</p>

<div class="divider"></div>

<h2 class="section-title" style="top:764px;font-size:15px">Featured Business Coupons</h2>

<div class="coupon" style="left:115px"><div class="coupon-art" role="img" aria-label="Green banknote-style gift coupon" style="background:radial-gradient(ellipse at 50% 50%,#f4f2e4 30%,#b7c49e 75%,#7f9468)"></div><h3>Coupon Tittle</h3><p>Lorem ipsum dolor sit amet</p><div class="price">$3,000</div></div>
<div class="coupon" style="left:254px"><div class="coupon-art" role="img" aria-label="Breakfast in bed coupon with red scroll border" style="background:radial-gradient(ellipse at 50% 50%,#fbf6ea 45%,#d9b49a 80%,#a23a2a)"></div><h3>Coupon Tittle</h3><p>Lorem ipsum dolor sit amet</p><div class="price">$3,000</div></div>
<div class="coupon" style="left:392px"><div class="coupon-art" role="img" aria-label="Cupcake shop twenty percent off coupon" style="background:linear-gradient(180deg,#6cc1c8 0%,#9ed3cf 40%,#efe4bd 60%,#e8d9a8 100%)"></div><h3>Coupon Tittle</h3><p>Lorem ipsum dolor sit amet</p><div class="price">$3,000</div></div>
<div class="coupon" style="left:531px"><div class="coupon-art" role="img" aria-label="Ten dollars off shopping coupon" style="background:linear-gradient(90deg,#fff7ee 0%,#fbeee0 55%,#e6ddd3 75%,#cfe3c5 100%)"></div><h3>Coupon Tittle</h3><p>Lorem ipsum dolor sit amet</p><div class="price">$3,000</div></div>

<section class="partners">
  <span class="partner" style="left:196px">Granvale</span>
  <span class="partner" style="left:334px;display:flex;align-items:center;gap:7px"><span style="width:15px;height:15px;border-radius:50%;background:#bdbdbd"></span>Deskloom</span>
  <span class="partner" style="left:535px">Ortex</span>
</section>

<footer class="site-footer">
  <div class="f-col" style="left:84px"><h4>SITE DIRECTORY</h4><ul><li>Search the Directory</li><li>Create a Directory Listing</li><li>Quote Finder</li><li>Coupons</li><li>Submit A Coupon</li><li>Advertise with us</li></ul></div>
  <div class="f-col" style="left:203px"><h4>SITE DIRECTORY</h4><ul><li>Join the Forum</li><li>Submit an Article or Video</li><li>Affiliates</li><li>Become an Affiliate</li><li>Case Studies</li><li>Help Guides</li></ul></div>
  <div class="f-col" style="left:325px"><h4>POPULAR CATEGORIES</h4><ul><li>Etiam est nunc</li><li>Venenatis tristique</li><li>Emperdiet ac nisl</li><li>Cum sociis natoque</li><li>Penatibus et magnis</li></ul></div>
  <div class="f-col" style="left:458px"><h4>ABOUT</h4><ul><li>About Us</li><li>Contact Us</li><li>Term &amp; Conditions</li><li>Privacy Policy</li><li>Supporting City Councils</li><li>Site Map</li></ul></div>
  <div class="f-col" style="left:570px"><h4>FOLLOW US</h4><div class="social"><i style="background:#c4302b"></i><i style="background:#3b5998"></i><i style="background:#3aa4d9"></i><i style="background:#0e76a8"></i></div><div class="subscribe">Subscribe to our Coupon Deals</div></div>
</footer>
<div class="footer-bottom"><p>© 2014 Company Name &nbsp;All right reserved &nbsp;Term of Use</p></div>

</body>
</html>
```